Website to design and sell sundials: www.gnomonvale.com

We have a website that creates a free paper sundial, we want to migrate from this not profit free website to a website where we will continue offering the free paper sundial model but We will also offer a manufactured sundial and sell it.
In order to understand the project, please visit:
http://www.gnomonvale.com/vertical/sundial.html and
http://www.torvel.net/landing/

The website user journey should be redesigned, including the phases that are,
select language
Show product give info
Creation/edit sundial (could be one or more phases)
View created sundial
Buy sundial.

May some of them could be combined or splitted, what It have more sense.

Requirements
Must have
• A description page user journey offering freemium paper sundial and physical sundial to sell.
• A sundial creation page for "free" paper sundial
• A result page for paper sundial
• A sell page for physical

```html
<!DOCTYPE html>
<html lang="en">
<head>
<meta charset="utf-8">
<title>GnomonVale – Sundial design</title>
<link href="https://fonts.googleapis.com/css2?family=Roboto:wght@300;400;500&family=Open+Sans:wght@400;600&display=swap" rel="stylesheet">
<style>
:root{
  --red:#c2211b;
  --red-dark:#a3130f;
  --orange:#f6b443;
  --ink:#333;
  --muted:#666;
  --line:#ddd;
  --panel:#f2f2f2;
  --white:#fff;
}
*{box-sizing:border-box;margin:0;padding:0}
html,body{width:801px;height:1200px;overflow:hidden;background:var(--white)}
body{position:relative;font-family:"Open Sans",sans-serif;color:var(--ink)}
.abs{position:absolute}
.top-rule{left:0;top:0;width:801px;height:2.4px;background:var(--red)}
.brand{left:66px;top:38px;display:flex;align-items:center;gap:8px;font-family:"Roboto",sans-serif;font-weight:500;font-size:19px;color:var(--red)}
.brand-dot{width:14px;height:14px;border-radius:50%;background:var(--red)}
.phone{left:538px;top:40px;display:flex;align-items:center;gap:6px;font-size:10.5px;color:var(--red)}
.lang{left:654px;top:35px;width:80px;height:26px;border:1px solid var(--line);border-radius:2px;display:flex;align-items:center;gap:5px;padding-left:7px;font-size:9.5px;color:#555}
.flag{width:19px;height:11px;background:#2a3f8f}
.nav{left:0;top:91px;width:801px;height:35px;background:linear-gradient(#c9241d,#a9140f)}
.nav a{position:absolute;top:0;height:35px;line-height:35px;font-family:"Roboto",sans-serif;font-size:8.8px;color:#fff;text-decoration:none;text-align:center}
.nav .home{left:66px;width:98px;background:var(--orange)}
.nav .sep{position:absolute;top:0;width:1px;height:35px;background:rgba(0,0,0,.12)}
.hero{left:0;top:126px;width:801px;height:308px;background:linear-gradient(180deg,#c9c7b8 0%,#e7d8b4 22%,#c7b38a 34%,#7d9a45 48%,#5f8a2e 75%,#7a8f3e 100%)}
.hero h1{position:absolute;left:66px;top:82px;width:340px;font-family:"Roboto",sans-serif;font-weight:300;font-size:21px;line-height:22px;color:#fff}
.hero p{position:absolute;left:66px;top:131px;width:320px;font-size:8.5px;line-height:17px;color:#fff}
.btn{background:var(--red);color:#fff;font-size:9.5px;text-align:center;border-radius:2px}
.hero .btn{position:absolute;left:66px;top:172px;width:98px;height:29px;line-height:29px;font-family:"Roboto",sans-serif}
.shade{left:0;top:434px;width:801px;height:20px;background:linear-gradient(rgba(0,0,0,.08),rgba(0,0,0,0))}
.map{left:66px;top:464px;width:281px;height:235px;background:radial-gradient(ellipse at 60% 55%,#8c7a4a 0%,#4b5a36 35%,#1c3c5a 70%,#12304e 100%)}
.h2{font-family:"Roboto",sans-serif;font-weight:300;font-size:21px;color:#333}
.h2 span{color:var(--red)}
.loc-title{left:370px;top:460px}
.rule{height:1.5px;background:#555}
.intro{left:369px;top:497px;width:365px;font-size:8px;line-height:14.5px;color:#555}
.field{background:#fff;border:1px solid var(--line);font-size:8px;color:#777;padding-left:8px;display:flex;align-items:center}
.go{left:623px;top:530px;width:59px;height:23px;line-height:23px}
.coords{left:369px;top:566px;width:365px;height:134px;background:var(--panel)}
.label{font-size:8px;color:#555}
.options-bg{left:0;top:737px;width:801px;height:385px;background:var(--panel)}
.card{left:60px;top:816px;width:674px;height:269px;background:#fff;border:1px solid #e2e2e2}
.photo{background:linear-gradient(90deg,#3a3530,#8a6a55 40%,#c79a82 100%);border:2px solid #fff;outline:1px solid #ccc}
.photo.win{background:linear-gradient(90deg,#1d1b18 0%,#6f7a84 35%,#c8bba9 60%,#9aa6b0 100%)}
.kind{background:var(--panel);width:151px;height:110px;padding:14px 10px}
.kind h3{font-family:"Roboto",sans-serif;font-weight:300;font-size:15px;color:#333;margin-bottom:5px}
.kind p{font-size:8px;line-height:12.8px;color:#555}
.radio{width:7px;height:7px;border:1px solid #aaa;border-radius:50%;background:#fff}
.radio.on{background:radial-gradient(#2b4c85 35%,#fff 45%)}
.check{width:8px;height:8px;border:1px solid #aaa;background:#fff}
.footer{left:0;top:1122px;width:801px;height:78px;background:var(--red-dark)}
.footer .t{position:absolute;font-size:8px;color:#fff}
.social{width:26px;height:26px;border-radius:50%;background:#2a62a8;border:2px solid #d8dde8}
</style>
</head>
<body>
<div class="abs top-rule"></div>

<header>
  <div class="abs brand"><span class="brand-dot"></span>GnomonVale.com</div>
  <div class="abs phone">
    <svg width="19" height="19" viewBox="0 0 19 19"><circle cx="9.5" cy="9.5" r="8.3" fill="none" stroke="#f6b443" stroke-width="1.6"/><path d="M6.5 5.5l2 2-1 1.2c.7 1.3 1.6 2.2 2.8 2.8l1.2-1 2 2-1.3 1.3c-3-.4-6.6-4-7-7z" fill="#f6b443"/></svg>
    (305)-555 0142
  </div>
  <div class="abs lang"><span class="flag"></span>English
    <svg width="6" height="4" viewBox="0 0 6 4"><path d="M0.5 0.5l2.5 2.5 2.5-2.5" fill="none" stroke="#888"/></svg>
  </div>
</header>

<nav class="abs nav">
  <a class="home" href="#">HOME</a>
  <a href="#" style="left:164px;width:158px">WHAT YOU NEED</a>
  <span class="sep" style="left:316px"></span>
  <a href="#" style="left:316px;width:130px">PRODUCTS</a>
  <span class="sep" style="left:446px"></span>
  <a href="#" style="left:446px;width:140px">ABOUT US</a>
  <span class="sep" style="left:586px"></span>
  <a href="#" style="left:586px;width:152px">CONTACT US</a>
  <span class="sep" style="left:738px"></span>
</nav>

<section class="abs hero" role="img" aria-label="Photo of a large stone sundial on a grassy clifftop above a sandy beach">
  <h1>Manuafacture your Sundial, design to your specific location</h1>
  <p>Sundials are instruments that tell you the time with the shadow of the sun. To design a sundial you need to know exactly where you are going to put</p>
  <div class="btn">Order now</div>
  <svg class="abs" style="left:22px;top:120px" width="12" height="34" viewBox="0 0 12 34"><path d="M11 1L1 17l10 16" fill="none" stroke="#fff" stroke-width="1.2"/></svg>
  <svg class="abs" style="left:758px;top:120px" width="12" height="34" viewBox="0 0 12 34"><path d="M1 1l10 16L1 33" fill="none" stroke="#fff" stroke-width="1.2"/></svg>
</section>
<div class="abs shade"></div>

<section class="location">
  <div class="abs map" role="img" aria-label="Satellite map of Europe and Africa for picking the sundial location">
    <div class="abs" style="left:17px;top:11px;width:56px;height:18px;background:#fff;font-size:6.5px;display:flex;align-items:center;gap:8px;padding-left:5px;color:#555">Map <b style="color:#000;font-weight:600">Satellite</b></div>
    <div class="abs" style="left:259px;top:174px;width:16px;height:48px;background:#fff;font-size:11px;text-align:center;line-height:22px;color:#555">+<br>−</div>
  </div>

  <div class="abs h2 loc-title">Sundial <span>location</span></div>
  <div class="abs rule" style="left:370px;top:486px;width:150px"></div>
  <p class="abs intro">Select the location where you want to place your paper sundial, mark a line along building wall where you want to put it.Write your address and press Go! (e.g. Picadilly circus, london, UK)</p>
  <div class="abs field" style="left:369px;top:530px;width:246px;height:23px"></div>
  <div class="abs btn go">Go</div>

  <div class="abs coords"></div>
  <div class="abs field" style="left:378px;top:580px;width:108px;height:22px">Longitude:</div>
  <div class="abs field" style="left:495px;top:580px;width:109px;height:22px">Latitude:</div>
  <div class="abs field" style="left:613px;top:580px;width:109px;height:22px">Wall declination:</div>
  <div class="abs" style="left:378px;top:616px;width:109px;height:70px;background:#fff">
    <svg width="109" height="70" viewBox="0 0 109 70"><text x="52.5" y="18" font-size="5" font-family="sans-serif">N</text><path d="M54.5 20v36" stroke="#000" stroke-width="1.3"/><path d="M52 25l2.5-5 2.5 5z" fill="#000"/></svg>
  </div>
  <div class="abs label" style="left:494px;top:618px">Now select the face of the building</div>
  <div class="abs label" style="left:500px;top:641px">Face:</div>
  <div class="abs field" style="left:526px;top:637px;width:51px;height:21px;padding-left:14px">A
    <span style="position:absolute;left:35px;top:0;width:1px;height:19px;background:var(--line)"></span>
    <svg class="abs" style="left:39px;top:8px" width="7" height="4" viewBox="0 0 7 4"><path d="M0 0h7L3.5 4z" fill="#555"/></svg>
  </div>
</section>

<section>
  <div class="abs options-bg"></div>
  <div class="abs h2" style="left:0;width:801px;text-align:center;top:764px">Sundial <span>options</span></div>
  <div class="abs rule" style="left:330px;top:796px;width:140px"></div>

  <div class="abs card"></div>

  <div class="abs photo" style="left:78px;top:834px;width:160px;height:110px" role="img" aria-label="Photo of a paper sundial fixed to a brick wall"></div>
  <div class="abs kind" style="left:238px;top:834px">
    <h3>Wall sundial</h3>
    <p>Sundials are instruments that tell you the time with the shadow of the sun to design a sundial</p>
    <div class="radio on" style="margin:8px 0 0 5px"></div>
  </div>

  <div class="abs photo win" style="left:78px;top:954px;width:160px;height:112px" role="img" aria-label="Photo of a paper sundial taped to a window"></div>
  <div class="abs kind" style="left:238px;top:954px;height:112px">
    <h3>Window sundial</h3>
    <p>Sundials are instruments that tell you the time with the shadow of the sun to design a sundial</p>
    <div class="radio" style="margin:8px 0 0 5px"></div>
  </div>

  <div class="abs label" style="left:426px;top:851px">Banner :</div>
  <div class="abs field" style="left:462px;top:845px;width:108px;height:21px">Paper sundial</div>

  <div class="abs label" style="left:426px;top:897px">Solar Time:</div>
  <div class="abs radio" style="left:488px;top:899px"></div>
  <div class="abs label" style="left:551px;top:897px">Solar Time:</div>
  <div class="abs radio on" style="left:609px;top:898px"></div>

  <div class="abs label" style="left:428px;top:936px">Daylight Saving Time:</div>
  <div class="abs check" style="left:512px;top:937px"></div>

  <div class="abs label" style="left:428px;top:970px">Timezone</div>
  <div class="abs field" style="left:510px;top:966px;width:206px;height:21px">(GM+999)LOCAL TIME (SOLAR TIME)
    <span style="position:absolute;left:186px;top:0;width:1px;height:19px;background:var(--line)"></span>
    <svg class="abs" style="left:192px;top:8px" width="7" height="4" viewBox="0 0 7 4"><path d="M0 0h7L3.5 4z" fill="#555"/></svg>
  </div>

  <div class="abs label" style="left:428px;top:1004px">Equation of time</div>
  <div class="abs check" style="left:512px;top:1006px"></div>

  <div class="abs btn" style="left:426px;top:1034px;width:98px;height:30px;line-height:30px">Create sundial</div>
</section>

<footer class="abs footer">
  <span class="t" style="left:66px;top:22px">Home</span>
  <span class="t" style="left:105px;top:22px">/</span>
  <span class="t" style="left:122px;top:22px">What you need</span>
  <span class="t" style="left:193px;top:22px">/</span>
  <span class="t" style="left:208px;top:22px">Products</span>
  <span class="t" style="left:256px;top:22px">/</span>
  <span class="t" style="left:271px;top:22px">About us</span>
  <span class="t" style="left:320px;top:22px">/</span>
  <span class="t" style="left:334px;top:22px">Contact us</span>
  <span class="t" style="left:66px;top:46px">© 2016 gnomonvale. All right reserved</span>
  <span class="abs social" style="left:645px;top:27px"></span>
  <span class="abs social" style="left:676px;top:27px;background:#3aa3dd"></span>
  <span class="abs social" style="left:706px;top:27px;background:#1f6aa6"></span>
  <span class="t" style="left:759px;top:35px">C12</span>
</footer>
</body>
</html>
```